BLS Business Card 2018

Larkmere Chiropractic. We have two locations that we want to advertise on the same card. Brightvale OrthoCore campus address: 3815 Pellham Dr., Suite 240, Flowood, MS 39417. Madison address: 246 Willowmere Dr., Building D., Madison, MS 39284. website: www.drlarkmere-example.com. o:(601)555-0147 f:(601)555-0183

Target Market(s)

Health care decision makers: primary care doctors and mothers

Contact Information for Business Card

I have no idea; up for any suggestions and I'd do much better picking from examples versus describing what I'm looking for. We are in a very high end location and would like the cards to look really sharp.

Requirements
Must have
• My name, Martin R Belvane, D.C.

```html
<!DOCTYPE html>
<html lang="en">
<head>
<meta charset="utf-8">
<title>Larkmere Chiropractic – Business Card</title>
<link rel="stylesheet" href="https://fonts.googleapis.com/css2?family=Lora:wght@400;500;600&display=swap">
<style>
  :root {
    --backdrop: #e4e4e4;
    --navy: #0c5a7f;
    --teal: #3eacbd;
    --white: #ffffff;
    --ink: #3d3d3d;
    --ink-soft: #5c5c5c;
    --brand-blue: #155f86;
    --art-light: #e6eff4;
    --art-mid: #c9dce7;
  }
  * { box-sizing: border-box; margin: 0; padding: 0; }
  html, body { width: 1200px; height: 852px; overflow: hidden; }
  body {
    background: var(--backdrop);
    font-family: "Lora", Georgia, serif;
    position: relative;
  }
  .card {
    position: absolute;
    width: 540px;
    height: 310px;
    border-radius: 22px;
    overflow: hidden;
    box-shadow: 0 6px 18px rgba(0,0,0,0.18);
  }

  /* Front */
  .card--front { left: 90px; top: 110px; background: var(--navy); color: var(--white); }
  .brand {
    position: absolute; left: 0; right: 0; top: 52px;
    display: flex; align-items: center; justify-content: center; gap: 18px;
  }
  .brand__dot { width: 40px; height: 40px; border-radius: 50%; background: var(--white); }
  .brand__name {
    font-size: 36px; font-weight: 500; line-height: 1.02; letter-spacing: 1px;
    text-transform: uppercase; color: var(--white);
  }
  .locations {
    position: absolute; left: 0; right: 0; top: 170px; height: 72px;
    background: var(--teal);
  }
  .campus-pill {
    position: absolute; left: 50%; top: -14px; transform: translateX(-50%);
    background: var(--navy); border: 1.5px solid var(--white); border-radius: 16px;
    padding: 5px 22px; font-size: 13px; font-weight: 600; white-space: nowrap;
  }
  .locations__divider {
    position: absolute; left: 50%; top: 22px; width: 1px; height: 38px;
    background: rgba(255,255,255,0.6);
  }
  .address {
    position: absolute; top: 24px; font-size: 12.5px; line-height: 1.35;
    display: flex; gap: 8px; align-items: flex-start;
  }
  .address--left { right: calc(50% + 16px); text-align: right; flex-direction: row; }
  .address--right { left: calc(50% + 16px); }
  .address svg { flex: none; margin-top: 2px; }
  .website {
    position: absolute; left: 0; right: 0; top: 262px;
    display: flex; align-items: center; justify-content: center; gap: 14px;
    font-size: 13px; letter-spacing: 0.3px;
  }
  .website__rule { width: 50px; height: 1.5px; background: var(--white); }

  /* Back */
  .card--back { left: 570px; top: 430px; background: var(--white); color: var(--ink); }
  .figure-art {
    position: absolute; right: 0; top: 0; width: 250px; height: 100%;
    background: linear-gradient(160deg, var(--art-light), var(--art-mid));
  }
  .back-brand {
    position: absolute; left: 32px; top: 46px; display: flex; align-items: center; gap: 12px;
  }
  .back-brand__dot { width: 26px; height: 26px; border-radius: 50%; background: var(--ink); }
  .back-brand__name {
    font-size: 27px; font-weight: 500; line-height: 1.02; letter-spacing: 0.8px;
    text-transform: uppercase; color: var(--ink);
  }
  .person { position: absolute; left: 32px; top: 150px; }
  .person__name { font-size: 19px; font-weight: 600; color: var(--brand-blue); }
  .person__role { font-size: 11px; color: var(--ink-soft); margin-top: 1px; }
  .contacts { position: absolute; left: 32px; top: 206px; list-style: none; }
  .contacts li {
    display: flex; align-items: center; gap: 12px;
    font-size: 13px; line-height: 18px; color: var(--ink-soft);
  }
  .contacts svg { flex: none; }
</style>
</head>
<body>

<section class="card card--front">
  <div class="brand">
    <span class="brand__dot"></span>
    <div class="brand__name">Larkmere<br>Chiropractic</div>
  </div>

  <div class="locations">
    <div class="campus-pill">OrthoCore Campus</div>
    <div class="locations__divider"></div>
    <div class="address address--left">
      <svg width="11" height="14" viewBox="0 0 11 14" aria-hidden="true"><path d="M5.5 0A5.5 5.5 0 0 0 0 5.5C0 9.5 5.5 14 5.5 14S11 9.5 11 5.5A5.5 5.5 0 0 0 5.5 0Zm0 7.7a2.2 2.2 0 1 1 0-4.4 2.2 2.2 0 0 1 0 4.4Z" fill="#fff"/></svg>
      <span>3815 Pellham Dr., Suite 240,<br>Flowood, MS 39417</span>
    </div>
    <div class="address address--right">
      <svg width="11" height="14" viewBox="0 0 11 14" aria-hidden="true"><path d="M5.5 0A5.5 5.5 0 0 0 0 5.5C0 9.5 5.5 14 5.5 14S11 9.5 11 5.5A5.5 5.5 0 0 0 5.5 0Zm0 7.7a2.2 2.2 0 1 1 0-4.4 2.2 2.2 0 0 1 0 4.4Z" fill="#fff"/></svg>
      <span>246 Willowmere Dr., Building D.,<br>Madison, MS 39284</span>
    </div>
  </div>

  <div class="website">
    <span class="website__rule"></span>
    <span>www.drlarkmere-example.com</span>
    <span class="website__rule"></span>
  </div>
</section>

<section class="card card--back">
  <div class="figure-art" role="img" aria-label="Line drawing of a human back and shoulders"></div>

  <div class="back-brand">
    <span class="back-brand__dot"></span>
    <div class="back-brand__name">Larkmere<br>Chiropractic</div>
  </div>

  <div class="person">
    <div class="person__name">Martin R Belvane, D.C.</div>
    <div class="person__role">Managing Director</div>
  </div>

  <ul class="contacts">
    <li>
      <svg width="12" height="12" viewBox="0 0 12 12" aria-hidden="true"><path d="M2.4 0.6 4.2 2.6 3.3 4.1C4 5.6 6.4 8 7.9 8.7L9.4 7.8 11.4 9.6 10.4 11.4C5.6 11.4 0.6 6.4 0.6 1.6Z" fill="#155f86"/></svg>
      <span>(601)555-0147</span>
    </li>
    <li>
      <svg width="12" height="12" viewBox="0 0 12 12" aria-hidden="true"><rect x="3" y="0.5" width="6" height="4" fill="#155f86"/><rect x="0.5" y="4" width="11" height="5" rx="1" fill="#155f86"/><rect x="3" y="8" width="6" height="3.5" fill="#155f86" stroke="#fff" stroke-width="0.8"/></svg>
      <span>(601)555-0183</span>
    </li>
    <li>
      <svg width="12" height="12" viewBox="0 0 12 12" aria-hidden="true"><rect x="0.5" y="2" width="11" height="8" fill="#155f86"/><path d="M0.8 2.3 6 6.5 11.2 2.3" fill="none" stroke="#fff" stroke-width="1"/></svg>
      <span>m.r.belvane@drlarkmere-example.com</span>
    </li>
    <li>
      <svg width="12" height="12" viewBox="0 0 12 12" aria-hidden="true"><circle cx="6" cy="6" r="5.5" fill="#155f86"/><path d="M0.5 6H11.5M6 0.5C3.5 3.5 3.5 8.5 6 11.5M6 0.5C8.5 3.5 8.5 8.5 6 11.5" fill="none" stroke="#fff" stroke-width="0.8"/></svg>
      <span>www.drlarkmere-example.com</span>
    </li>
  </ul>
</section>

</body>
</html>
```